Quick Straightforward Billboard Redesign

- Design billboard sized for 10 foot' x 36' foot width live area size and please include bleeds 6" around all sides
- Exact blue color match is imperative in headline, logo, phone number bubble or wherever used. C-83 / M-45 / Y-1 / K-0-
- What I hope to illustrate is that our company offers the best porch screening in the area area, in regards to quality, expertise, durability, storms proof, but we do not build screen porches.
- Current board is attached below from previous designer, and as you can see sizing was off, white space on edges make it appear to be sized incorrectly.
- I also attached my own little mock up idea well well if it helps, favorite image, logo, headline, etc and ideas perhaps on expanding or making this better?

Thanks so much!

Target Market(s)

Drivers and passengers, Southeastern NC, are of immense new construction and high end homes.

Industry/Entity Type

Construction

Colors
0054AA
0677BA
7BADD7
CADEEF
E8F1F8

Requirements
Must have
• Blue color matching
Nice to have
• Design spins or other thoughts on my little mock up

```html
<!DOCTYPE html>
<html lang="en">
<head>
<meta charset="utf-8">
<title>Coastway Screening Billboard</title>
<link href="https://fonts.googleapis.com/css2?family=Montserrat:wght@800;900&display=swap" rel="stylesheet">
<style>
  :root {
    --page-bg: #cae7fa;
    --board-white: #f7f7f5;
    --brand-blue: #0054aa;
    --headline-blue: #0d66b3;
    --band-light: #5aa5d6;
    --band-dark: #0a5cb0;
    --accent-green: #1fba5e;
    --photo-sky: #9cc8e8;
    --photo-ground: #8d8a80;
    --white: #ffffff;
  }
  * { margin: 0; padding: 0; box-sizing: border-box; }
  html, body { width: 1200px; height: 873px; overflow: hidden; }
  body { background: var(--page-bg); font-family: "Montserrat", Arial, sans-serif; }
  .billboard {
    position: absolute; left: 40px; top: 281px;
    width: 1120px; height: 311px;
    background: var(--board-white); overflow: hidden;
  }
  .billboard-shapes { position: absolute; inset: 0; }
  .headline {
    position: absolute; left: 58px; top: 24px;
    font-weight: 900; font-size: 60px; line-height: 55px;
    color: var(--headline-blue); letter-spacing: 0.5px;
  }
  .headline .highlight { color: var(--accent-green); }
  .phone {
    position: absolute; left: 50px; top: 211px;
    display: flex; align-items: center; gap: 14px;
    color: var(--white); font-weight: 800; font-size: 68px; line-height: 1;
  }
  .phone svg { width: 54px; height: 54px; flex: none; }
  .brand-name {
    position: absolute; right: 34px; top: 264px;
    font-weight: 800; font-size: 22px; line-height: 26px;
    color: var(--brand-blue); white-space: nowrap;
  }
</style>
</head>
<body>
  <div class="billboard">
    <svg class="billboard-shapes" viewBox="0 0 1120 311" width="1120" height="311">
      <defs>
        <linearGradient id="bandGradient" x1="0" y1="0" x2="1" y2="0">
          <stop offset="0" stop-color="var(--band-light)"/>
          <stop offset="1" stop-color="var(--band-dark)"/>
        </linearGradient>
        <linearGradient id="photoGradient" x1="0" y1="0" x2="0" y2="1">
          <stop offset="0" stop-color="var(--photo-sky)"/>
          <stop offset="0.45" stop-color="#7fa86a"/>
          <stop offset="1" stop-color="var(--photo-ground)"/>
        </linearGradient>
      </defs>
      <polygon class="phone-band" points="0,198 714,198 742,311 0,311" fill="url(#bandGradient)"/>
      <polygon class="porch-photo" role="img" aria-label="Photo of a screened porch with wicker lounge chairs overlooking a lawn and lake"
               points="700,52 1090,52 1090,244 744,244 790,150" fill="url(#photoGradient)"/>
      <polyline class="chevron" points="672,48 770,150 708,262" fill="none" stroke="var(--accent-green)" stroke-width="14" stroke-linejoin="miter"/>
    </svg>

    <h1 class="headline">YOUR<br>SCREEN PORCH<br><span class="highlight">EXPERTS.</span></h1>

    <div class="phone">
      <svg viewBox="0 0 54 54" aria-hidden="true">
        <circle cx="27" cy="27" r="24" fill="none" stroke="var(--white)" stroke-width="3.5"/>
        <path d="M18 15c2-1 3 0 4 2l2 4c1 2 0 3-1 4l-1 1c1 3 4 6 7 7l1-1c1-1 2-2 4-1l4 2c2 1 3 2 2 4-1 3-4 4-7 3-8-2-14-8-16-16-1-3 0-7 1-9z" fill="var(--white)"/>
        <path d="M31 17a7 7 0 0 1 6 6M31 12a12 12 0 0 1 11 11" fill="none" stroke="var(--white)" stroke-width="2.5" stroke-linecap="round"/>
      </svg>
      <span class="phone-number">910.555.0142</span>
    </div>

    <div class="brand-name">COASTWAY SCREENING</div>
  </div>
</body>
</html>
```